Website redesign for job agency recruitment

Please refer to the attached document, “Tarvenly Work Website Brief,” for comprehensive details regarding the scope, objectives, and requirements of this website redesign project.

For imagery you can use images from this website https://www.pixelmarrowfoto.com or any other you regularly use.

Target Market(s)

Jobseekers and Companies looking for general labour

Industry/Entity Type

Services: Oil, Gas and Mining, Administrative, Construction and Trades, Warehouse and Logistics and, Manufacturing.

Number of Pages Required

5+ page

Font styles to use
Serif
Other font styles liked:
• Inter, Open-Sans or similar.

Requirements
Must have
• The requirements highlighted in the Word document attached. The final design needs to be provided in Figma including all viewports (Desktop, mobiel and tablet)
Should not have
• Website we like as a reference: www.brevicktalentco.com, www.qelvaworks.com, www.zunmarra.com, www.ferrowhires.com, www.9vtalentpool.com, www.hiringwithtrello.ca

```html
<!DOCTYPE html>
<html lang="en">
<head>
<meta charset="utf-8">
<title>Tarvenly Work Agency — Workforce Solutions</title>
<link href="https://fonts.googleapis.com/css2?family=Montserrat:wght@600;700&family=Lato:wght@400;700&display=swap" rel="stylesheet">
<style>
:root{
  --blue:#1a3f9c;
  --blue-dark:#12307a;
  --yellow:#f7b918;
  --yellow-soft:#e2b219;
  --ink:#4a4a4a;
  --text:#444;
  --gray:#f4f4f4;
  --white:#fff;
}
*{box-sizing:border-box;margin:0;padding:0}
html,body{width:1200px;height:3462px;overflow:hidden}
body{position:relative;background:var(--white);font-family:'Lato',sans-serif;color:var(--text)}
.abs{position:absolute}
.heading{font-family:'Montserrat',sans-serif;font-weight:700}
.eyebrow{font-family:'Montserrat',sans-serif;font-weight:600;color:var(--yellow);font-size:22px;letter-spacing:.3px}

/* header */
.site-header{left:0;top:0;width:1200px;height:95px;background:var(--white);z-index:5}
.brand{left:110px;top:32px;z-index:6;display:flex;align-items:center;gap:10px}
.brand-dot{width:14px;height:14px;border-radius:50%;background:var(--yellow)}
.brand-name{font-family:'Lato',sans-serif;font-weight:700;color:var(--blue);font-size:22px;line-height:28px}
.nav a{position:absolute;top:36px;font-size:15px;color:#333;text-decoration:none}
.nav a.active{color:var(--blue);font-weight:700}
.nav a.active::after{content:"";position:absolute;left:12px;right:12px;top:24px;height:2px;background:var(--blue)}

/* hero */
.hero-photo{left:0;top:95px;width:1200px;height:805px;background:linear-gradient(180deg,#2a3c62 0%,#485a7c 35%,#8a6a55 60%,#2b2f3c 100%)}
.hero-title{left:110px;top:300px;font-size:46px;line-height:58px;color:var(--white)}
.hero-title span{color:var(--yellow);display:block}
.hero-lead{left:110px;top:436px;width:500px;font-size:23px;line-height:30px;color:var(--white)}
.btn{position:absolute;display:flex;align-items:center;justify-content:center;border-radius:22px;font-size:17px;color:var(--white)}
.btn-blue{background:var(--blue)}
.btn-yellow{background:var(--yellow)}
.dots{left:1139px;top:440px}
.dots i{display:block;width:10px;height:10px;border:1.5px solid var(--white);border-radius:50%;margin-bottom:7.5px}
.dots i.on{background:var(--white)}

/* about */
.about-arc{left:112px;top:924px;width:462px;height:450px;border-radius:50%;border-left:12px solid var(--yellow);border-bottom:6px solid var(--yellow)}
.about-photo{left:127px;top:925px;width:444px;height:444px;border-radius:50%;background:linear-gradient(135deg,#7d8fa6,#c9a488 55%,#3d4a5e)}
.about-title{left:667px;top:1034px;font-size:40px;color:var(--ink)}
.about-text{left:670px;top:1107px;width:417px;font-size:17px;line-height:25.7px;text-align:justify;color:#3b3b3b}

/* services */
.services-bg{left:0;top:1400px;width:1200px;height:1100px;background:var(--gray)}
.center-text{left:0;width:1200px;text-align:center}
.services-title{top:1660px;font-size:40px;color:var(--ink)}
.services-lead{top:1720px;font-size:17px;line-height:26px;color:#3b3b3b}
.hub-photo{left:414px;top:1808px;width:376px;height:376px;border-radius:50%;background:linear-gradient(160deg,#6f6a66,#3d4c6e 45%,#c49a2a 75%,#2e3038)}
.icon-badge{position:absolute;width:94px;height:94px;border-radius:50%;background:var(--white);display:flex;align-items:center;justify-content:center}
.icon-badge.blue{width:80px;height:80px;background:var(--blue)}
.svc h3{font-family:'Montserrat',sans-serif;font-weight:700;color:var(--blue);font-size:19px;margin-bottom:8px}
.svc p{font-size:15px;line-height:23px;color:#444;text-align:justify}
.svc.right{text-align:right}
.svc.right p{text-align-last:right}

/* network */
.network-bg{left:0;top:2430px;width:1200px;height:605px;background:linear-gradient(90deg,#d9aa16,var(--yellow-soft) 50%,#e0b11c)}
.network-title{top:2728px;font-size:40px;color:var(--white)}
.network-lead{top:2790px;font-size:17px;line-height:26px;color:var(--white)}

/* footer */
.site-footer{left:0;top:3035px;width:1200px;height:427px;background:linear-gradient(90deg,#1a49b0,#143a8e 60%,#12307a);color:var(--white)}
.foot-h{position:absolute;font-size:21px;font-weight:700}
.foot-l{position:absolute;font-size:15.5px;line-height:26px}
.social{position:absolute;top:3306px;width:38px;height:38px;border-radius:6px}
.divider{left:110px;top:3414px;width:977px;height:1px;background:rgba(255,255,255,.35)}
</style>
</head>
<body>

<header class="abs site-header">
  <nav class="nav">
    <a class="active" style="left:477px">Home</a>
    <a style="left:560px">Candidates</a>
    <a style="left:678px">Companies</a>
    <a style="left:795px">About Us</a>
    <a style="left:900px">Contact</a>
    <a style="left:996px">Forms &amp; Links</a>
  </nav>
</header>
<div class="abs brand">
  <span class="brand-dot"></span>
  <span class="brand-name">Tarvenly Work Agency Ltd.</span>
</div>

<section>
  <div class="abs hero-photo" role="img" aria-label="Two engineers in hard hats and hi-vis jackets reviewing a laptop beside an oil pumpjack at dusk"></div>
  <h1 class="abs heading hero-title"><span>Workforce Solutions</span>Built for Performance</h1>
  <p class="abs hero-lead">From industrial projects to corporate offices, we provide qualified professionals ready to make an immediate impact.</p>
  <a class="btn btn-blue" style="left:110px;top:559px;width:180px;height:43px">For Candidates</a>
  <a class="btn btn-yellow" style="left:298px;top:559px;width:180px;height:43px">For Employers</a>
  <div class="abs dots"><i class="on"></i><i></i><i></i><i></i></div>
  <svg class="abs" style="left:0;top:690px" width="1200" height="215" viewBox="0 0 1200 215">
    <path d="M0,92 C120,40 240,25 420,40 C650,60 820,210 1000,195 C1100,185 1160,150 1200,128 L1200,215 L0,215 Z" fill="#f7b918"/>
    <path d="M0,168 C130,70 280,55 450,70 C660,90 820,215 1000,205 C1100,198 1160,170 1200,150 L1200,215 L0,215 Z" fill="#fff"/>
  </svg>
</section>

<section>
  <div class="abs about-arc"></div>
  <div class="abs about-photo" role="img" aria-label="Two colleagues smiling while reviewing a document together in an office"></div>
  <div class="abs eyebrow" style="left:669px;top:998px">ABOUT US</div>
  <h2 class="abs heading about-title">Tarvenly Work Agency</h2>
  <p class="abs about-text">Tarvenly Work is a trusted staffing partner delivering skilled workforce solutions across Canada’s most essential industries. We specialize in connecting qualified professionals with employers in Oil &amp; Gas, Mining, Construction &amp; Trades, Warehouse &amp; Logistics, Manufacturing, and Administrative sectors.</p>
  <a class="btn btn-blue" style="left:670px;top:1298px;width:155px;height:42px">Read More</a>
</section>

<section>
  <div class="abs services-bg"></div>
  <svg class="abs" style="left:0;top:1390px" width="1200" height="170" viewBox="0 0 1200 170">
    <path d="M0,0 L1200,0 L1200,25 C1100,20 1000,10 870,40 C700,80 560,160 340,162 C180,164 60,120 0,70 Z" fill="#fff"/>
  </svg>
  <div class="abs eyebrow center-text" style="top:1628px">OUR SERVICES</div>
  <h2 class="abs heading center-text services-title">Professional Staffing Solutions</h2>
  <p class="abs center-text services-lead">We specialize in connecting qualified professionals with employers in Oil &amp; Gas, Mining, Construction &amp;<br>Trades, Warehouse &amp; Logistics, Manufacturing, and Administrative sectors.</p>

  <div class="abs hub-photo" role="img" aria-label="Two factory workers in hard hats checking a tablet in an industrial plant"></div>

  <div class="icon-badge" style="left:387px;top:1852px"><svg width="48" height="48" viewBox="0 0 48 48" fill="#f7b918"><rect x="4" y="12" width="8" height="32"/><rect x="14" y="22" width="8" height="22"/><path d="M22 44V28l10-6v6l10-6v22Z"/><rect x="5" y="4" width="6" height="6"/></svg></div>
  <div class="icon-badge" style="left:724px;top:1852px"><svg width="54" height="48" viewBox="0 0 54 48" fill="#f7b918"><rect x="6" y="10" width="26" height="18" rx="2"/><circle cx="40" cy="12" r="7"/><rect x="2" y="30" width="50" height="4"/><rect x="2" y="38" width="50" height="3"/></svg></div>
  <div class="icon-badge" style="left:387px;top:2039px"><svg width="48" height="48" viewBox="0 0 48 48" fill="#f7b918"><path d="M4 20 24 6l20 14v24H4Z"/><rect x="14" y="24" width="20" height="20" fill="#fff"/><rect x="16" y="32" width="7" height="10"/><rect x="25" y="32" width="7" height="10"/><rect x="20" y="24" width="8" height="7"/></svg></div>
  <div class="icon-badge" style="left:724px;top:2039px"><svg width="48" height="48" viewBox="0 0 48 48" fill="#f7b918"><rect x="10" y="6" width="5" height="38"/><rect x="4" y="8" width="40" height="5"/><rect x="36" y="13" width="2" height="12"/><rect x="24" y="26" width="20" height="18"/><rect x="4" y="42" width="40" height="3"/></svg></div>
  <div class="icon-badge blue" style="left:562px;top:2151px"><svg width="46" height="44" viewBox="0 0 46 44" fill="#f7b918"><rect x="6" y="10" width="6" height="30"/><path d="M12 40V24l10-6v6l10-6v6l10-6v22Z"/><rect x="4" y="40" width="40" height="3"/></svg></div>

  <div class="abs svc right" style="left:114px;top:1860px;width:251px"><h3>Oil, Gas &amp; Mining</h3><p>Providing safety-certified, skilled professionals for demanding industrial environments.</p></div>
  <div class="abs svc" style="left:834px;top:1860px;width:252px"><h3>Administrative Services</h3><p>Professional office support to keep your business organized and productive.</p></div>
  <div class="abs svc right" style="left:114px;top:2047px;width:251px"><h3>Warehouse &amp; Logistics</h3><p>Reliable workforce solutions to support fast-moving supply chain operations.</p></div>
  <div class="abs svc" style="left:836px;top:2047px;width:251px"><h3>Construction &amp; Trades</h3><p>Supplying experienced tradespeople to keep projects on schedule and on budget.</p></div>
  <div class="abs svc" style="left:477px;top:2255px;width:251px;text-align:center"><h3>Manufacturing</h3><p style="text-align-last:center">Qualified production and technical staff to maintain efficiency and quality standards.</p></div>
</section>

<section>
  <div class="abs network-bg" role="img" aria-label="Worker in a hard hat at an oil field, overlaid with a yellow tint"></div>
  <svg class="abs" style="left:0;top:2395px" width="1200" height="160" viewBox="0 0 1200 160">
    <path d="M0,0 L1200,0 L1200,42 C1080,110 980,150 820,140 C620,128 420,10 250,6 C140,4 50,40 0,75 Z" fill="#f4f4f4"/>
    <path d="M0,75 C50,40 140,4 250,6 C420,10 620,128 820,140 C980,150 1080,110 1200,42 L1200,62 C1090,135 990,162 820,155 C620,146 420,35 250,30 C140,27 50,62 0,95 Z" fill="#1a3f9c"/>
  </svg>
  <div class="abs center-text" style="top:2694px;font-family:'Montserrat',sans-serif;font-weight:600;font-size:22px;color:var(--blue)">JOIN OUR NETWORK</div>
  <h2 class="abs heading center-text network-title">Find Your Next Opportunity</h2>
  <p class="abs center-text network-lead">We offer career opportunities and workforce solutions across Oil &amp; Gas, Construction, Logistics, Manufacturing, and<br>Administrative sectors. Our team is committed to matching the right talent with the right opportunity.</p>
  <a class="btn btn-blue" style="left:511px;top:2872px;width:179px;height:42px">Apply Now</a>
</section>

<footer class="abs site-footer"></footer>
<div class="foot-h" style="left:110px;top:3148px;color:#fff">Get Job Alerts</div>
<div class="foot-l" style="left:110px;top:3202px;width:250px;color:#fff">Text SUBSCRIBE to 778-555-0142 (BC) or 403-555-0187 (AB) for job alerts.</div>
<div class="social" style="left:117px;background:var(--yellow)" aria-label="Social profile"></div>
<div class="social" style="left:172px;top:3310px;width:30px;height:30px;border:2px solid #fff;background:transparent" aria-label="Social profile"></div>

<div class="foot-h" style="left:450px;top:3130px;color:#fff">Main Links</div>
<div class="foot-l" style="left:450px;top:3184px;color:#fff;line-height:38.5px">Home<br>Candidates<br>Companies<br>About Us</div>

<div class="foot-h" style="left:646px;top:3130px;color:#fff">Contact Us</div>
<svg class="abs" style="left:646px;top:3186px" width="20" height="24" viewBox="0 0 20 24" fill="none" stroke="#fff" stroke-width="1.8"><path d="M10 22s8-7.5 8-13a8 8 0 0 0-16 0c0 5.5 8 13 8 13Z"/><circle cx="10" cy="9" r="2.5"/></svg>
<div class="foot-l" style="left:687px;top:3184px;width:230px;color:#fff">123 Harlow Street, Suite 12456.</div>
<svg class="abs" style="left:646px;top:3258px" width="20" height="20" viewBox="0 0 20 20" fill="none" stroke="#fff" stroke-width="1.8"><path d="M4 2h4l2 5-2.5 1.5a11 11 0 0 0 4 4L13 10l5 2v4a2 2 0 0 1-2 2A16 16 0 0 1 2 4a2 2 0 0 1 2-2Z"/></svg>
<div class="foot-l" style="left:687px;top:3256px;color:#fff">1-888-555-0163</div>
<svg class="abs" style="left:646px;top:3308px" width="20" height="16" viewBox="0 0 20 16" fill="none" stroke="#fff" stroke-width="1.8"><rect x="1" y="1" width="18" height="14" rx="2"/><path d="m1 3 9 6 9-6"/></svg>
<div class="foot-l" style="left:687px;top:3303px;color:#fff">info@tarvenlywork.com</div>

<div class="foot-h" style="left:956px;top:3130px;color:#fff">Other Links</div>
<div class="foot-l" style="left:956px;top:3184px;color:#fff;line-height:38.5px">Contact<br>Forms &amp; Links<br>Terms &amp; Conditions<br>Privacy Policy</div>

<div class="abs divider"></div>
<div class="abs center-text" style="top:3430px;font-size:13px;color:#fff">Copyright © 2026 Tarvenly Work Agency. All rights reserved.</div>

</body>
</html>
```